Fancy flyer to entice High School Students

http://kestrelvane.com needs a marketing slick/flyer to pass out. The marketing text is below(feel free to place where you think appropriate).

* 8th grade to 12th grade (or 8th graders to 12th graders)
* Land a real job internship(instead of Pelkroft)
* 100's of internships available
* Learn how to start your own business out of High School making way more than minimum wage
* In college when interviewing for an internship don't be the guy that answers "no, sorry, this would be my first internship" putting you at a huge disadvantage"
* Fill in the Contact Us form at http://kestrelvane.com at the bottom left corner to find out more information

We will be evaluating design with this blog post in mind....
http://trundlepostnotes.com/color-influence-buyers/

We like attention grabbing contact us type stuff and calls to action. If you feel it is appropriate to change the marketing text to make your flyer stand out, please feel free. I am not the best at marketing and am the first to admit it.
Updates

A simple 8.5 x 11 flyer would be great.

Target Market(s)

High School students, male and female with high grade point averages(smart students). For the top 20% of their class.

Industry/Entity Type

Marketing

Requirements
Must have
• good call to action

```html
<!DOCTYPE html>
<html lang="en">
<head>
<meta charset="utf-8">
<title>Kestrelvane Software – Internship Flyer</title>
<link rel="stylesheet" href="https://fonts.googleapis.com/css2?family=Jost:wght@400;500&family=Roboto+Condensed:wght@400&family=Archivo:ital,wght@1,700&display=swap">
<style>
  :root {
    --page-bg: #e8e5e1;
    --ink: #2b2b2b;
    --logo-ink: #333333;
    --brand-red: #e71c24;
    --panel-dark: #323a40;
    --panel-text: #d9dcde;
    --white: #ffffff;
    --wall: #ecebe6;
    --wall-shade: #dedcd5;
    --board: #8a9890;
    --board-soft: #b4beb7;
  }
  html, body {
    margin: 0;
    padding: 0;
    width: 1200px;
    height: 1027px;
    overflow: hidden;
    background: var(--page-bg);
  }
  .flyer {
    position: absolute;
    left: 20px;
    top: 62px;
    width: 1160px;
    height: 902px;
    overflow: hidden;
    box-shadow: 0 4px 14px rgba(0,0,0,.25);
    background: var(--wall);
  }
  .flyer-photo {
    position: absolute;
    inset: 0;
    background:
      radial-gradient(ellipse 420px 300px at 540px 420px, rgba(138,152,144,.55), rgba(138,152,144,0) 100%),
      linear-gradient(90deg, var(--wall) 0%, var(--wall-shade) 10%, var(--board-soft) 20%, var(--board) 45%, var(--board-soft) 72%, var(--wall-shade) 82%, var(--wall) 95%),
      var(--wall);
    background-blend-mode: normal;
  }
  .flyer-photo::after {
    content: "";
    position: absolute;
    inset: 0;
    background: linear-gradient(180deg, var(--wall) 0%, rgba(236,235,230,.85) 14%, rgba(236,235,230,0) 32%);
  }
  .brand-bar {
    position: absolute;
    left: 0;
    top: 16px;
    width: 555px;
    height: 111px;
    background: var(--white);
    box-shadow: 0 4px 6px rgba(0,0,0,.35);
    display: flex;
    align-items: center;
    padding-left: 16px;
    box-sizing: border-box;
  }
  .brand-name {
    font-family: "Jost", sans-serif;
    font-weight: 500;
    font-size: 46px;
    color: var(--logo-ink);
    letter-spacing: .5px;
  }
  .phone {
    position: absolute;
    left: 628px;
    top: 56px;
    display: flex;
    align-items: center;
    gap: 36px;
  }
  .phone-number {
    font-family: "Archivo", sans-serif;
    font-style: italic;
    font-weight: 700;
    font-size: 43px;
    color: var(--ink);
  }
  .panels {
    position: absolute;
    inset: 0;
  }
  .headline {
    font-family: "Jost", sans-serif;
    font-size: 35px;
    font-weight: 400;
    fill: var(--white);
  }
  .point {
    font-family: "Jost", sans-serif;
    font-size: 16.5px;
    fill: var(--white);
  }
  .contact {
    font-family: "Roboto Condensed", sans-serif;
    fill: var(--panel-text);
  }
  .contact-address { font-size: 22px; }
  .contact-web { font-size: 21px; }
</style>
</head>
<body>
  <main class="flyer">
    <div class="flyer-photo" role="img" aria-label="Photo of cheering students with raised arms in front of a classroom chalkboard, a teacher beside them"></div>

    <header class="brand-bar">
      <span class="brand-name">Kestrelvane Software</span>
    </header>

    <div class="phone">
      <svg width="60" height="60" viewBox="0 0 60 60" aria-hidden="true">
        <circle cx="30" cy="30" r="26" fill="none" stroke="var(--brand-red)" stroke-width="4"/>
        <path d="M24 16 l6 0 l0 9 l-4 2 q1 5 4 9 l4 -2 l0 9 l-6 0 q-9 -12 -4 -27 z" fill="var(--brand-red)"/>
      </svg>
      <span class="phone-number">(555) 201-4837</span>
    </div>

    <svg class="panels" viewBox="0 0 1160 902" width="1160" height="902">
      <polygon points="0,622 318,564 381,902 0,902" fill="var(--panel-dark)"/>
      <polygon points="318,564 1160,400 1160,783 381,902" fill="var(--brand-red)"/>

      <g class="offer" transform="translate(346 603) rotate(-11)">
        <text class="headline" x="0" y="0">WE PROVIDE REAL INTERSHIP!</text>
        <g fill="var(--white)">
          <circle cx="27" cy="36" r="11"/>
          <circle cx="27" cy="76" r="11"/>
          <circle cx="27" cy="116" r="11"/>
          <circle cx="27" cy="157" r="11"/>
          <circle cx="27" cy="200" r="11"/>
        </g>
        <text class="point" x="50" y="36">8th grade to 12th grade (or 8th graders to 12th graders)</text>
        <text class="point" x="50" y="76">Land a real job internship (instead of Pelkroft)</text>
        <text class="point" x="50" y="116">100's of internships available</text>
        <text class="point" x="50" y="157">Learn how to start your own business out of High School making way more than minimum wage</text>
        <text class="point" x="50" y="200">In college when interviewing for an internship don't be the guy that answers "no, sorry, this would</text>
        <text class="point" x="50" y="221">be my first internship" putting you at a huge disadvantage"</text>
      </g>

      <g class="contact-icons">
        <path d="M2 716 l25 -24 l25 24 l-7 0 l0 24 l-13 0 l0 -14 l-10 0 l0 14 l-13 0 l0 -24 z" fill="var(--panel-text)"/>
        <g transform="translate(23 779) rotate(-11)" fill="none" stroke="var(--panel-text)" stroke-width="3">
          <rect x="0" y="0" width="44" height="28" rx="2"/>
          <path d="M2 2 l20 15 l20 -15"/>
        </g>
        <g fill="none" stroke="var(--panel-text)" stroke-width="2.5">
          <circle cx="50" cy="843" r="19"/>
          <ellipse cx="50" cy="843" rx="8" ry="19"/>
          <line x1="31" y1="843" x2="69" y2="843"/>
          <line x1="34" y1="833" x2="66" y2="833"/>
          <line x1="34" y1="853" x2="66" y2="853"/>
        </g>
      </g>

      <g class="contact">
        <text class="contact-address" transform="translate(68 703) rotate(-11)">4180 W. Larkmoor Ave. #214</text>
        <text class="contact-address" transform="translate(74 734) rotate(-11)">Denhollow, CO 80099</text>
        <text class="contact-web" transform="translate(88 785) rotate(-11)">www.kestrelvane.com</text>
        <text class="contact-web" transform="translate(92 836) rotate(-11)">info@kestrelvane.com</text>
      </g>
    </svg>
  </main>
</body>
</html>
```